Willow Cradle Pregnancy and Baby Massage

I need a web design for a new business, WILLOW CRADLE PREGNANCY AND BABY MASSAGE that I am in the process of setting up in the suburbs of Perth, Western Australia. The business is owned and operated by myself and my intention is to service Pregnant Mothers and Parents of Young Babies that would benefit from massage. I would like to have a "Home Page" and pages for "About Me", "Pregnancy Massage", "Baby Massage", a Pricing Page for Pregnancy Massage Sessions, a Pricing Page for Baby Massage Sessions, and a "Contact Me" page to allow clients to either contact me with queries or book available pregnancy massage sessions on a particular day of the week. I would also like a "News" page that would include articles I have written, news about new courses and a link to my Facebook page (yet to be set up). I would like to keep the colour schemes similar to my logo design colours. I need the design to be easy to follow and to appeal to a younger audience (20's to mid 30's).
The target audience is pregnant mothers-to-be wishing to receive massage treatments, and new parents and grandparents of small babies that would like to learn how to massage their babies.
The look and feel should be modern, professional, elegant and feminine.
I need the design to be in a standard format such that I can update the content by myself ( and does not need specialised software) as the company and business progresses.

Target Market(s)

Contact Information for Business Card

Card should have rounded edges. Design should have the same "feel" as the website. Contact Details of my business address, mobile phone, email and website should be included.

Font styles to use
Script

Requirements
Must have
• Same colours as logo design. In cmyk system, the colours are: 20,60,0,0 which best result is pantone 681 and 40,40,0,0 which best result is pantone 2645. Card should include the logo design.

```html
<!DOCTYPE html>
<html lang="en">
<head>
<meta charset="utf-8">
<title>Willow Cradle Pregnancy and Baby Massage</title>
<link rel="stylesheet" href="https://fonts.googleapis.com/css2?family=Poppins:wght@400;500;600;700&family=Roboto:wght@400&display=swap">
<style>
:root{
  --pink:#b565a5;
  --pink-light:#cf8cc0;
  --lavender:#8d80bd;
  --ink:#3a3a3a;
  --text:#555;
  --muted:#888;
  --footer:#f2f1f2;
  --white:#fff;
}
*{box-sizing:border-box;margin:0;padding:0}
html,body{width:718px;height:1200px;overflow:hidden;background:var(--white)}
body{font-family:"Poppins",sans-serif;color:var(--text);position:relative}
.abs{position:absolute}

/* header */
.call{left:58px;top:36px;display:flex;align-items:center;gap:8px}
.call svg{width:24px;height:24px}
.call-text{border-left:1px solid #ccc;padding-left:7px;font-family:"Roboto",sans-serif;color:#666;line-height:1.15}
.call-text small{font-size:9px;display:block}
.call-text b{font-weight:400;font-size:12.5px;color:#555;letter-spacing:.3px}
.brand{left:258px;top:20px;width:200px;text-align:center}
.brand-dot{width:26px;height:26px;border-radius:50%;background:var(--pink);margin:0 auto 6px}
.brand-name{font-size:11px;font-weight:500;color:var(--pink);line-height:1.25}
.search{left:520px;top:34px;width:138px;height:21px;border:1px solid #ccc;border-radius:2px;font-size:7px;color:#555;padding:6px 6px;display:flex;justify-content:space-between;align-items:center}

/* nav */
.nav{left:0;top:90px;width:718px;height:32px;background:linear-gradient(#cf8bc1,#ac5c9d);border-bottom:1px solid #7d3f70;display:flex;padding-left:59px}
.nav a{color:var(--white);text-decoration:none;font-size:9.5px;font-weight:500;line-height:32px;padding:0 11px}
.nav a.active{background:#3b3b3b;padding:0 13px}

/* hero */
.hero{left:0;top:122px;width:718px;height:320px;background:linear-gradient(100deg,#e9e5df 0%,#ddd8cf 45%,#c9d7c2 62%,#a9c7d4 75%,#c9b49f 100%)}
.hero-title{left:58px;top:213px;font-size:22.5px;font-weight:700;color:var(--ink);line-height:1.26;letter-spacing:.4px}
.btn{left:58px;top:309px;width:73px;height:23px;background:var(--pink);color:var(--white);font-size:9px;font-weight:500;text-align:center;line-height:23px;border-radius:2px}
.arrow{width:21px;height:21px;border-radius:50%;background:#4a4a4a;top:254px}
.arrow svg{width:21px;height:21px}

/* welcome */
.welcome{left:0;top:485px;width:718px;text-align:center}
.welcome svg{width:30px;height:28px}
.welcome h2{font-size:18.5px;font-weight:600;line-height:1.3;letter-spacing:.5px;margin-top:4px}
.welcome h2 .a{color:var(--lavender);display:block}
.welcome h2 .b{color:var(--pink);display:block}
.welcome p{width:540px;margin:14px auto 0;font-size:7.2px;line-height:1.9;color:#444}

/* cards */
.card{top:645px;width:289px;height:269px;border:1px solid #ddd;box-shadow:0 1px 3px rgba(0,0,0,.12);background:var(--white);overflow:hidden}
.card .photo{height:154px}
.card .body{padding:17px 16px 0;font-size:6.6px;line-height:2;text-align:center;color:#444}
.card .body p+p{margin-top:7px}

/* footer */
.footer-bg{left:0;top:960px;width:718px;height:206px}
.badge{left:58px;top:1038px;width:108px;height:62px;border-radius:8px;background:#e9dbe6}
.social{left:58px;top:1115px;display:flex;gap:4px}
.social span{width:14px;height:14px;border-radius:50%;border:1px solid #999}
.col-title{font-size:11px;font-weight:500;color:#333;letter-spacing:.4px}
.contact{left:203px;top:1029px}
.contact ul{list-style:none;margin-top:12px}
.contact li{display:flex;gap:8px;font-size:7px;line-height:1.75;color:#444;margin-bottom:7px}
.contact li svg{width:10px;height:10px;flex:none;margin-top:2px}
.contact li.big{font-size:8px}
.news{left:381px;top:1029px;width:170px}
.news p{font-size:6.6px;line-height:1.75;color:#555;margin-top:12px}
.news form{display:flex;margin-top:10px;height:25px}
.news .field{flex:1;border:1px solid #ddd;background:var(--white);font-size:6.8px;padding:8px 8px;color:#555}
.news .sub{width:52px;background:var(--pink);color:var(--white);font-size:7.5px;text-align:center;line-height:25px}
.links{left:582px;top:1029px}
.links ul{list-style:none;margin-top:11px}
.links li{font-size:6.6px;line-height:13.3px;color:#444}
.bottom{left:0;top:1165px;width:718px;height:35px;background:var(--pink);color:var(--white);font-size:6.5px;text-align:center;line-height:35px}
</style>
</head>
<body>

<div class="abs call">
  <svg viewBox="0 0 24 24"><circle cx="12" cy="12" r="11" fill="none" stroke="#b565a5" stroke-width="1.3"/><path d="M8 7l2 0 1 3-1.4 1c.8 1.6 2 2.8 3.6 3.6l1-1.4 3 1v2c0 .6-.5 1-1 1C10.6 17 7 13.4 7 8c0-.5.4-1 1-1z" fill="none" stroke="#b565a5" stroke-width="1.1"/></svg>
  <div class="call-text"><small>Call Now :</small><b>08 6100 4273</b></div>
</div>

<div class="abs brand">
  <div class="brand-dot"></div>
  <div class="brand-name">Willow Cradle<br>Pregnancy and Baby Massage</div>
</div>

<div class="abs search"><span>SEARCH</span>
  <svg width="8" height="8" viewBox="0 0 10 10"><circle cx="4" cy="4" r="3" fill="none" stroke="#333" stroke-width="1.5"/><path d="M6.2 6.2L9 9" stroke="#333" stroke-width="1.5"/></svg>
</div>

<nav class="abs nav">
  <a class="active">Home</a><a>About Me</a><a>Pregnancy Massage</a><a>Baby Massage</a><a>Pricing</a><a>News</a><a>Contact Me</a>
</nav>

<div class="abs hero" role="img" aria-label="Therapist giving a shoulder massage to a pregnant woman seated on the floor of a bright studio with exercise balls"></div>
<svg class="abs" style="left:0;top:402px" width="718" height="46" viewBox="0 0 718 46">
  <path d="M0 22 Q170 40 330 30 Q350 29 358 40 Q366 29 386 30 Q560 36 718 14 L718 46 L0 46Z" fill="#fff"/>
  <path d="M0 22 Q170 40 330 30 Q350 29 358 40 Q366 29 386 30 Q560 36 718 14" fill="none" stroke="#d9d9d9" stroke-width="2"/>
</svg>

<div class="abs hero-title">WILLOW CRADLE<br>PREGNANCY &amp; BABY<br>MASSAGE</div>
<div class="abs btn">READ MORE</div>
<div class="abs arrow" style="left:18px"><svg viewBox="0 0 21 21"><path d="M12 6l-4 4.5 4 4.5" fill="none" stroke="#fff" stroke-width="1.6"/></svg></div>
<div class="abs arrow" style="left:659px"><svg viewBox="0 0 21 21"><path d="M9 6l4 4.5-4 4.5" fill="none" stroke="#fff" stroke-width="1.6"/></svg></div>

<section class="abs welcome">
  <svg viewBox="0 0 30 28"><path d="M15 26C6 19 2 14 2 8.5 2 4.8 4.8 2 8.3 2c2.8 0 4.8 1.6 6.7 4 1.9-2.4 3.9-4 6.7-4C25.2 2 28 4.8 28 8.5 28 14 24 19 15 26z" fill="none" stroke="#b565a5" stroke-width="3"/></svg>
  <h2><span class="a">WELCOME TO</span><span class="b">WILLOW CRADLE PREGNANCY &amp; BABY MASSAGE</span></h2>
  <p>Sed ut perspiciatis unde omnis iste natus error sit voluptatem accusantium doloremque laudantium, totam rem aperiam, eaque ipsa quae ab illo inventore veritatis et quasi architecto beatae vitae dicta sunt explicabo. Nemo enim ipsam voluptatem quia voluptas sit aspernatur aut odit aut fugit, sed quia consequuntur magni dolores eos qui ratione voluptatem sequi nesciunt. Neque porro quisquam est, qui dolorem</p>
</section>

<article class="abs card" style="left:59px">
  <div class="photo" role="img" aria-label="Two newborn babies sleeping wrapped in a peach cloth on a lace heart" style="background:linear-gradient(135deg,#a58a8c,#c9a9a0 50%,#8e7478)"></div>
  <div class="body"><p>Willow Cradle Pregnancy and Baby Massage was launched in 2017, offering massage for pregnant women, and instruction of baby massage to parents, grandparents and carers.</p></div>
</article>

<article class="abs card" style="left:370px">
  <div class="photo" role="img" aria-label="Two newborn babies cuddled together in a fur-lined basket" style="background:linear-gradient(135deg,#6d5440,#a88a6e 50%,#5a4536)"></div>
  <div class="body"><p>My vision is to provide a professional massage service to pregnant mothers and babies that also benefits from my skills and experience as a midwife. My expectation is that after each session, my clients should leave feeling relaxed, calm, emotionally nurtured, soothed and supported.</p><p>At all times, I will take the utmost care of your privacy, safety and comfort in what is a very personal, intimate time in your life.</p></div>
</article>

<svg class="abs footer-bg" viewBox="0 0 718 206">
  <path d="M0 40 Q170 30 320 14 Q350 10 358 22 Q366 10 396 14 Q560 35 718 22 L718 206 L0 206Z" fill="#f2f1f2"/>
  <path d="M0 40 Q170 30 320 14 Q350 10 358 22 Q366 10 396 14 Q560 35 718 22" fill="none" stroke="#b565a5" stroke-width="2"/>
</svg>

<div class="abs badge"></div>
<div class="abs social"><span></span><span></span><span></span><span></span></div>

<div class="abs contact">
  <div class="col-title">CONTACT US</div>
  <ul>
    <li><svg viewBox="0 0 10 10"><path d="M5 9.5S1.5 5.8 1.5 3.6a3.5 3.5 0 017 0C8.5 5.8 5 9.5 5 9.5z" fill="#b565a5"/><circle cx="5" cy="3.6" r="1.2" fill="#f2f1f2"/></svg><span>Willow Cradle Pregnancy &amp; Baby Massage<br>14 Banksia Grove Rd, Unit 3<br>Perth, Australia</span></li>
    <li class="big"><svg viewBox="0 0 10 10"><path d="M2 1h2l1 2.5-1.2 1c.6 1.2 1.5 2.1 2.7 2.7l1-1.2L10 7v2H9C4.6 9 1 5.4 1 1z" fill="#b565a5"/></svg><span>Phone: +61-8-6100-4273</span></li>
    <li class="big"><svg viewBox="0 0 10 10"><rect x="1" y="2" width="8" height="6" fill="#b565a5"/><path d="M1 2l4 3.5L9 2" fill="none" stroke="#f2f1f2" stroke-width=".8"/></svg><span>Email: hello@willowcradle.example</span></li>
  </ul>
</div>

<div class="abs news">
  <div class="col-title">SIGN UP FOR NEWSLETTER</div>
  <p>Sed ut perspiciatis unde omnis iste natus error sit voluptatem accusantium doloremque laudantium</p>
  <form><div class="field">Enter Name</div><div class="sub">SUBSCRIBE</div></form>
</div>

<div class="abs links">
  <div class="col-title">QUICK LINKS</div>
  <ul><li>Home</li><li>About Me</li><li>Pregnancy Massage</li><li>Baby Massage</li><li>Pricing</li><li>News</li><li>Contact Me</li></ul>
</div>

<footer class="abs bottom">©2017 &nbsp;Willow Cradle Pregnancy &amp; Baby Massage. All Rights Reserved.</footer>

</body>
</html>
```